Animal Eye Clinic needs a Business card

We are a new veterinary ophthalmology practice (Ridgeline Pet Vision Care) and we need a business card designed. We only see animal eyes - we are not a regular veterinary clinic. We already have a logo. We are looking for a professional, good looking business card to hand out to our clients. We are looking for something simple but professional and contemporary. Our logo is likely the only picture/graphic that needs to be on the card.
Updates

Contact Information for Business Card

Delia Vossman, BSc, DVM, MSc, DipACVO
Veterinary Ophthalmologist

Phone: 250.418.3927
Email: ridgelinepetvisioncare@mailbox-example.net
Website: ridgelinepetvisioncare-example.net
Address: 1874 Thornbury Rd
Kelowna, BC, V1X 4M9

Colors

Designer to choose colors to be used in the design.

Requirements
Must have
• Our logo (attached)

```html
<!DOCTYPE html>
<html lang="en">
<head>
<meta charset="utf-8">
<title>Ridgeline Pet Vision Care – Business Card</title>
<link href="https://fonts.googleapis.com/css2?family=Roboto:wght@400;500&display=swap" rel="stylesheet">
<style>
  :root {
    --backdrop: #1b1b1b;
    --card: #2b2b2b;
    --card-edge: #232323;
    --teal: #1a9bb0;
    --silver: #8a8a8a;
    --text: #f2f2f2;
  }
  * { margin: 0; padding: 0; box-sizing: border-box; }
  html, body { width: 1200px; height: 900px; overflow: hidden; }
  body {
    background: radial-gradient(ellipse at 50% 40%, #2c2c2c 0%, var(--backdrop) 75%);
    font-family: "Roboto", Arial, sans-serif;
    color: var(--text);
  }
  .canvas {
    position: relative;
    width: 1200px;
    height: 900px;
  }
  .card {
    position: absolute;
    left: 260px;
    width: 680px;
    height: 388px;
    background: linear-gradient(160deg, #303030 0%, var(--card) 50%, var(--card-edge) 100%);
    border-bottom: 7px solid var(--teal);
    box-shadow: 0 18px 40px rgba(0,0,0,0.55);
    overflow: hidden;
  }
  .card-front { top: 42px; }
  .card-back  { top: 470px; }

  .brand {
    display: flex;
    align-items: center;
    gap: 14px;
  }
  .brand-dot {
    width: 34px;
    height: 34px;
    border-radius: 50%;
  }
  .brand-name {
    font-weight: 500;
    letter-spacing: 0.5px;
  }

  .card-front .brand {
    position: absolute;
    inset: 0;
    justify-content: center;
  }
  .card-front .brand-dot { background: var(--silver); width: 46px; height: 46px; }
  .card-front .brand-name { color: var(--silver); font-size: 32px; }

  .card-back .brand {
    position: absolute;
    top: 40px;
    right: 36px;
  }
  .card-back .brand-dot { background: var(--teal); }
  .card-back .brand-name { color: var(--teal); font-size: 24px; }

  .person {
    position: absolute;
    top: 104px;
    right: 36px;
    text-align: right;
  }
  .person-name {
    color: var(--teal);
    font-size: 38px;
    font-weight: 500;
    line-height: 1.1;
  }
  .person-credentials,
  .person-role {
    font-size: 16px;
    line-height: 1.4;
  }

  .contact {
    position: absolute;
    top: 228px;
    right: 36px;
    text-align: right;
    font-size: 15px;
    line-height: 1.6;
  }
  .contact .label { color: var(--teal); }
  .contact .sep { color: var(--teal); padding: 0 4px; }
  .contact .web-domain { font-weight: 500; }

  .divider {
    position: absolute;
    top: 290px;
    left: 36px;
    right: 36px;
    height: 2px;
    background: var(--teal);
  }

  .address {
    position: absolute;
    top: 314px;
    right: 36px;
    font-size: 17px;
  }
</style>
</head>
<body>
<main class="canvas">
  <section class="card card-front" aria-label="Card front">
    <div class="brand">
      <span class="brand-dot"></span>
      <span class="brand-name">Ridgeline Pet Vision Care</span>
    </div>
  </section>

  <section class="card card-back" aria-label="Card back">
    <div class="brand">
      <span class="brand-dot"></span>
      <span class="brand-name">Ridgeline Pet Vision Care</span>
    </div>

    <div class="person">
      <div class="person-name">Delia Vossman</div>
      <div class="person-credentials">BSc, DVM, MSc, DipACVO</div>
      <div class="person-role">Veterinary Ophthalmologist</div>
    </div>

    <div class="contact">
      <div><span class="label">P:</span> 250.418.3927<span class="sep">|</span><span class="label">E:</span> ridgelinepetvisioncare@mailbox-example.net</div>
      <div><span class="label">W:</span> www.<span class="web-domain">ridgelinepetvisioncare-example</span>.net</div>
    </div>

    <div class="divider"></div>

    <div class="address">Address: 1874 Thornbury Rd Kelowna, BC, V1X 4M9</div>
  </section>
</main>
</body>
</html>
```